Powerpoint Design for AI Consulting Company

Description
Velmora Quill Industries is a consulting and technology company that engineers AI transformations, automation, and decision intelligence for financial firms, mining companies, and supply chains.
We already have a logo and brand colors (see attached). We need a professional, modern PowerPoint template that reflects our brand identity and positioning.
Key Requirements
Use our logo and color palette (deep blue, orange, white/black backgrounds).
Clean, modern design with subtle technology-inspired elements (data flows, AI networks, abstract systems).
Must feel sophisticated, bold, and boardroom-ready for executive presentations.
Templates should support both dark and light backgrounds.
Deliverables
A reusable PowerPoint template (.PPTX) with at least these layouts:
Title / Cover slide – dramatic, logo placement, tagline space.
Agenda slide – clean, structured layout.
Section divider slides – strong use of brand colors.
Content slides – text + image, text + icon.
Charts & data slides – bar, line, pie, comparison table, infographics.
Case study / example project slide. - ROI / Transformation Journey
Timeline / roadmap slide.
Team profile slide.
Reframe Slide – A provocative insight that reframes the client’s current thinking.
Options & Trade-offs Slide – Matrix showing different paths and consequences.
Execution Roadmap Slide – Step-by-step phased implementation view.
Closing / thank-you slide with contact details.
Style Guide
Colors: Primary – deep blue (#0D3559), Secondary – orange (#E87722), Accents – silver/white.
Fonts: Modern sans-serif (e.g., Montserrat, Lato, or similar).
Visual elements: Abstract technology, data-inspired graphics, mathematical motifs. Avoid clutter or overly “sci-fi” looks.
Tone: Premium consulting + innovative AI firm.
Target Market(s)
Velmora Quill Industries’ target market is senior decision-makers in finance, mining, and supply chains, where complexity, risk, and ROI pressure are high. Primary buyers include family offices, boutique wealth managers, super funds, and mining/supply chain executives, who value insight-driven strategies, automation, and decision intelligence. A secondary market includes professional services (accounting, legal, medical) and regulated SMEs (daycare, aged care, community services) burdened by admin and compliance. The slide deck must appeal to a boardroom audience — authoritative, data-driven, and visually clean — while remaining flexible enough to adapt for SME professional services.
Look and feel
Each slider illustrates characteristics of the customer's brand and the style your logo design should communicate.

```html
<!DOCTYPE html>
<html lang="en">
<head>
<meta charset="utf-8">
<title>Velmora Quill Industries – Presentation Template</title>
<link href="https://fonts.googleapis.com/css2?family=Lato:wght@400;700;900&display=swap" rel="stylesheet">
<style>
:root{
  --page:#d9d9dc;
  --ink-black:#04070c;
  --navy-dark:#0a1a2f;
  --navy:#0d3559;
  --navy-mid:#12305a;
  --orange:#e87722;
  --white:#ffffff;
  --silver:#b9c3cf;
  --muted:#8e9bb0;
  --panel:rgba(255,255,255,0.07);
  --grid:rgba(255,255,255,0.14);
}
*{box-sizing:border-box;margin:0;padding:0}
html,body{width:905px;height:1200px;overflow:hidden}
body{background:var(--page);font-family:'Lato',Arial,sans-serif;color:var(--white);position:relative}
.slide{position:absolute;width:430px;height:242px;overflow:hidden;
  background:linear-gradient(125deg,var(--ink-black) 0%,var(--navy-dark) 45%,var(--navy) 100%);
  box-shadow:0 6px 16px rgba(0,0,0,0.25)}
.brand-mark{position:absolute;top:12px;right:14px;display:flex;align-items:center;gap:4px;
  font-size:5.5px;font-weight:700;color:var(--white);letter-spacing:.2px}
.brand-mark .dot{width:6px;height:6px;border-radius:50%;background:var(--white)}
.slide-title{position:absolute;left:20px;top:24px;font-size:12px;font-weight:700}
.abs{position:absolute}
.orange{color:var(--orange)}
/* cover */
.cover{background:linear-gradient(135deg,#0c2b5c 0%,#0b2148 55%,#0a1c3a 100%)}
.cover .network{position:absolute;inset:0;
  background:radial-gradient(ellipse 120px 90px at 62% 42%,rgba(40,170,160,0.35),transparent 70%),
             radial-gradient(ellipse 200px 140px at 70% 50%,rgba(30,90,140,0.35),transparent 75%)}
.cover h1{position:absolute;left:24px;top:96px;font-size:21px;font-weight:900;color:var(--orange)}
.cover h2{position:absolute;left:24px;top:124px;font-size:19px;font-weight:700}
/* agenda */
.agenda .lines{position:absolute;inset:0;background:radial-gradient(ellipse 260px 110px at 50% 80%,rgba(30,120,130,0.28),transparent 75%)}
.agenda-item{position:absolute;display:flex;align-items:center;gap:6px;font-size:7.5px;font-weight:700}
.num{width:8px;height:8px;border-radius:50%;background:var(--orange);font-size:4.5px;display:flex;align-items:center;justify-content:center;font-weight:900;color:var(--white)}
/* who */
.who p{position:absolute;left:20px;font-size:4.6px;line-height:1.65;width:140px}
.qmark{position:absolute;left:270px;top:40px;width:90px;height:150px;border-radius:40px 40px 20px 20px;
  background:radial-gradient(ellipse at 50% 40%,rgba(232,119,34,0.45),rgba(232,119,34,0.05) 70%,transparent)}
.feature{position:absolute;display:flex;align-items:center;gap:4px;font-size:4.4px}
.feature i{width:5px;height:5px;background:var(--orange);border-radius:1px;display:block}
/* expertise */
.intro{position:absolute;left:20px;top:48px;width:180px;font-size:5.4px;font-weight:700;line-height:1.3}
.card{position:absolute;width:95px;height:60px;background:var(--panel);padding:8px 6px 0 18px}
.card::before{content:"";position:absolute;left:0;top:0;width:8px;height:100%;background:var(--orange)}
.card h4{font-size:6px;font-weight:700;margin-bottom:7px}
.card p{font-size:4.4px;line-height:1.3;color:var(--silver)}
/* case */
.box{position:absolute;background:var(--panel);padding:6px 5px;font-size:3.9px;line-height:2.1;color:var(--silver)}
.box h5{font-size:4.6px;color:var(--white);display:flex;align-items:center;gap:3px}
.box h5 i{width:4px;height:4px;background:var(--orange);border-radius:50%;display:block}
/* roadmap */
.step{position:absolute;left:20px;width:172px;display:flex;align-items:flex-start;gap:5px;font-size:4px;line-height:1.3}
.step .num{flex:none;margin-top:0}
.step-text{flex:1}
.step-text b{display:block;font-size:4.6px;font-weight:700;margin-bottom:1px}
.step-text span{display:block;font-size:4px;color:var(--silver)}
/* team */
.member{position:absolute;width:90px;text-align:center;font-size:3.4px;line-height:1.3}
.avatar{width:24px;height:24px;border-radius:50%;background:var(--orange);margin:0 auto 4px}
.member b{display:block;font-size:4.6px;font-weight:400}
.member .role{font-size:3.6px;color:var(--orange);display:block;margin:2px 0}
.member small{display:block;font-size:3.4px;color:var(--silver)}
/* thanks */
.thanks h2{position:absolute;left:0;right:0;top:82px;text-align:center;font-size:25px;font-weight:900}
.contact{position:absolute;width:120px;text-align:center;font-size:3.8px}
.contact .ic{width:10px;height:10px;border-radius:50%;background:var(--orange);margin:0 auto 5px;display:flex;align-items:center;justify-content:center}
.contact b{display:block;font-size:5px;margin-bottom:2px}
</style>
</head>
<body>

<section class="slide cover" style="left:15px;top:86px">
  <div class="network" role="img" aria-label="Abstract teal AI network pattern"></div>
  <div class="brand-mark"><span class="dot"></span>Velmora Quill Industries</div>
  <h1>Velmora Quill Industries</h1>
  <h2>Engineering AI Transformations</h2>
</section>

<section class="slide agenda" style="left:460px;top:86px">
  <div class="lines" role="img" aria-label="Abstract data flow lines"></div>
  <div class="brand-mark"><span class="dot"></span>Velmora Quill Industries</div>
  <div class="slide-title" style="top:58px;font-size:10px">Agenda</div>
  <div class="agenda-item" style="left:20px;top:90px"><span class="num">1</span>Who We Are</div>
  <div class="agenda-item" style="left:20px;top:113px"><span class="num">3</span>Case Studies</div>
  <div class="agenda-item" style="left:20px;top:136px"><span class="num">5</span>Our Team</div>
  <div class="agenda-item" style="left:208px;top:90px"><span class="num">2</span>Our Expertise</div>
  <div class="agenda-item" style="left:208px;top:113px"><span class="num">4</span>Execution Roadmap</div>
  <div class="agenda-item" style="left:208px;top:136px"><span class="num">6</span>Contact Us</div>
</section>

<section class="slide who" style="left:15px;top:348px">
  <div class="brand-mark"><span class="dot"></span>Velmora Quill Industries</div>
  <div class="slide-title">Who We Are</div>
  <p style="top:50px"><span class="orange" style="font-size:5.5px">Velmora Quill Industries</span> is a consulting and technology company that engineers AI transformations, automation, and decision intelligence for financial firms, mining companies, and supply chains.</p>
  <p style="top:122px;width:200px">We deliver innovative solutions that help organizations improve their operations and make smarter decisions using cutting-edge AI technologies.</p>
  <div class="qmark" role="img" aria-label="Orange dotted question mark illustration"></div>
  <div class="feature" style="left:20px;top:166px"><i></i>Financial Performance Optimization</div>
  <div class="feature" style="left:120px;top:166px"><i></i>Complex Process Automation</div>
  <div class="feature" style="left:20px;top:184px"><i></i>Decision Intelligence Enhancement</div>
  <div class="feature" style="left:120px;top:184px"><i></i>Supply Chain Efficiency</div>
</section>

<section class="slide" style="left:460px;top:348px">
  <div class="brand-mark"><span class="dot"></span>Velmora Quill Industries</div>
  <div class="slide-title">Our Expertise</div>
  <div class="intro">We specialize in delivering AI, automation, and decision intelligence solutions tailored to meet the needs of the following sectors:</div>
  <div class="card" style="left:20px;top:97px"><h4>Financial Sector</h4><p>Risk management, investment analysis, and process automation</p></div>
  <div class="card" style="left:118px;top:97px"><h4>Mining Industry</h4><p>Extraction optimization, predictive maintenance, and resource management</p></div>
  <div class="card" style="left:20px;top:162px"><h4>Supply Chains</h4><p>Logistics optimization, demand forecasting, and inventory management</p></div>
  <div class="card" style="left:118px;top:162px"><h4>Professional Services</h4><p>Administrative task automation and customer service enhancement</p></div>
  <svg class="abs" style="left:225px;top:80px" width="200" height="130" viewBox="0 0 200 130" font-family="Lato,sans-serif" font-size="4.2" fill="#8e9bb0">
    <g fill="none" stroke="rgba(255,255,255,0.18)" stroke-width="0.5">
      <polygon points="100,15 140,38 140,84 100,107 60,84 60,38"/>
      <polygon points="100,35 123,48 123,74 100,87 77,74 77,48"/>
      <polygon points="100,55 106,58 106,64 100,67 94,64 94,58"/>
      <line x1="100" y1="15" x2="100" y2="107"/><line x1="60" y1="38" x2="140" y2="84"/><line x1="140" y1="38" x2="60" y2="84"/>
    </g>
    <polygon points="100,19 122,50 108,66 100,94 86,68 94,62" fill="rgba(232,119,34,0.35)" stroke="#e87722" stroke-width="0.8"/>
    <g fill="#e87722"><circle cx="100" cy="19" r="1.4"/><circle cx="122" cy="50" r="1.4"/><circle cx="108" cy="66" r="1.4"/><circle cx="100" cy="94" r="1.4"/><circle cx="86" cy="68" r="1.4"/><circle cx="94" cy="62" r="1.4"/></g>
    <text x="100" y="10" text-anchor="middle">Artificial Intelligence</text>
    <text x="145" y="38">Machine Learning</text>
    <text x="145" y="86">Process Automation</text>
    <text x="100" y="115" text-anchor="middle">Data Analytics</text>
    <text x="55" y="86" text-anchor="end">Decision Intelligence</text>
    <text x="55" y="38" text-anchor="end">Cloud Computing</text>
  </svg>
</section>

<section class="slide" style="left:15px;top:610px">
  <div class="brand-mark"><span class="dot"></span>Velmora Quill Industries</div>
  <div class="slide-title" style="top:20px">Case Study</div>
  <div class="abs orange" style="left:20px;top:37px;font-size:5.6px;font-weight:700">Supply Chain Optimization for Major Mining Company</div>
  <div class="abs" style="left:20px;top:52px;width:200px;font-size:4.3px;font-weight:700;line-height:1.6">We developed an integrated AI system to improve supply chain efficiency and reduce operational costs for a leading mining company.</div>
  <div class="box" style="left:20px;top:72px;width:100px;height:54px"><h5><i></i>Challenges</h5>Frequent supply chain delays<br>High inventory and storage costs<br>Difficulty forecasting future needs</div>
  <div class="box" style="left:20px;top:132px;width:100px;height:68px"><h5><i></i>Solutions</h5>Advanced ML forecasting system<br>Automated ordering and supply processes<br>Intelligent decision dashboards</div>
  <div class="abs" style="left:285px;top:48px;font-size:7px;font-weight:700">Results &amp; ROI</div>
  <svg class="abs" style="left:138px;top:58px" width="285" height="150" viewBox="0 0 285 150" font-family="Lato,sans-serif" font-size="3.8" fill="#ffffff">
    <rect x="110" y="1" width="12" height="3" fill="#5b6b80"/><text x="125" y="4">Before implementation</text>
    <rect x="190" y="1" width="12" height="3" fill="#e87722"/><text x="205" y="4">After implementation</text>
    <g text-anchor="end">
      <text x="24" y="16">100%</text><text x="24" y="28">90%</text><text x="24" y="40">80%</text><text x="24" y="52">70%</text><text x="24" y="64">60%</text><text x="24" y="76">50%</text><text x="24" y="88">40%</text><text x="24" y="100">30%</text><text x="24" y="112">20%</text><text x="24" y="124">10%</text><text x="24" y="136">0%</text>
    </g>
    <g fill="#5b6b80"><rect x="32" y="15" width="16" height="120"/><rect x="95" y="15" width="16" height="120"/><rect x="158" y="63" width="16" height="72"/><rect x="221" y="54" width="16" height="81"/></g>
    <g fill="#e87722"><rect x="52" y="45" width="16" height="90"/><rect x="115" y="60" width="16" height="75"/><rect x="178" y="21" width="16" height="114"/><rect x="241" y="27" width="16" height="108"/></g>
    <g text-anchor="middle"><text x="50" y="144">operating costs</text><text x="113" y="144">Delivery time</text><text x="176" y="144">Forecast accuracy</text><text x="239" y="144">Resource efficiency</text></g>
  </svg>
</section>

<section class="slide" style="left:460px;top:610px">
  <div class="brand-mark"><span class="dot"></span>Velmora Quill Industries</div>
  <div class="slide-title">Execution Roadmap</div>
  <div class="abs" style="left:20px;top:44px;width:170px;font-size:5.2px;line-height:1.25">We follow a structured, phased methodology for implementing AI and automation projects, ensuring successful and measurable outcomes.</div>
  <div class="step" style="top:82px"><span class="num">1</span><div class="step-text"><b>Assessment &amp; Analysis</b><span>Evaluating current state and identifying opportunities and challenges</span></div></div>
  <div class="step" style="top:106px"><span class="num">2</span><div class="step-text"><b>Solution Design</b><span>Developing a tailored strategy and implementation plan</span></div></div>
  <div class="step" style="top:128px"><span class="num">3</span><div class="step-text"><b>Development &amp; Testing</b><span>Building and testing solutions in a controlled environment</span></div></div>
  <div class="step" style="top:150px"><span class="num">4</span><div class="step-text"><b>Implementation &amp; Integration</b><span>Deploying solutions and integrating with existing systems</span></div></div>
  <div class="step" style="top:172px"><span class="num">5</span><div class="step-text"><b>Monitoring &amp; Optimization</b><span>Measuring results and continuous improvement</span></div></div>
  <svg class="abs" style="left:195px;top:50px" width="228" height="150" viewBox="0 0 228 150" font-family="Lato,sans-serif" font-size="3.6" fill="#ffffff">
    <rect x="70" y="3" width="9" height="3" fill="none" stroke="#e87722" stroke-width="0.6"/><text x="82" y="6">Effort Level</text>
    <rect x="113" y="3" width="9" height="3" fill="none" stroke="#ffffff" stroke-width="0.6"/><text x="125" y="6">Added Value</text>
    <g text-anchor="end"><text x="12" y="16">100%</text><text x="12" y="64">50%</text><text x="12" y="112">0%</text></g>
    <g stroke="rgba(255,255,255,0.08)" stroke-width="0.4"><line x1="15" y1="15" x2="220" y2="15"/><line x1="15" y1="63" x2="220" y2="63"/><line x1="15" y1="111" x2="220" y2="111"/></g>
    <polygon points="15,92 66,73 117,59 168,39 219,15 219,111 15,111" fill="rgba(120,140,170,0.25)"/>
    <path d="M15,82 C40,60 55,48 66,44 C85,32 100,18 117,20 C140,22 150,40 168,52 C190,66 205,80 219,87" fill="none" stroke="#e87722" stroke-width="1"/>
    <polyline points="15,92 66,73 117,59 168,39 219,15" fill="none" stroke="#ffffff" stroke-width="0.8"/>
    <g fill="#e87722"><circle cx="15" cy="82" r="1.4"/><circle cx="66" cy="44" r="1.4"/><circle cx="117" cy="20" r="1.4"/><circle cx="168" cy="52" r="1.4"/><circle cx="219" cy="87" r="1.4"/></g>
    <g fill="#ffffff"><circle cx="15" cy="92" r="1.4"/><circle cx="66" cy="73" r="1.4"/><circle cx="117" cy="59" r="1.4"/><circle cx="168" cy="39" r="1.4"/><circle cx="219" cy="15" r="1.4"/></g>
    <g text-anchor="middle"><text x="15" y="120">Assessment</text><text x="66" y="120">Design</text><text x="117" y="120">Development</text><text x="168" y="120">Implementation</text><text x="210" y="120">Monitoring</text></g>
  </svg>
</section>

<section class="slide" style="left:15px;top:872px">
  <div class="brand-mark"><span class="dot"></span>Velmora Quill Industries</div>
  <div class="slide-title">Our Team</div>
  <div class="abs" style="left:20px;top:44px;width:330px;font-size:5px;font-weight:700;line-height:1.7">Our team comprises experts in artificial intelligence, data science, and strategic consulting, with extensive experience in financial, mining, and supply chain sectors.</div>
  <div class="member" style="left:36px;top:76px"><div class="avatar" role="img" aria-label="Team member portrait placeholder"></div><b>Team Member 1</b><span class="role">Role 1</span><small>Brief description of expertise and experience.</small></div>
  <div class="member" style="left:170px;top:76px"><div class="avatar" role="img" aria-label="Team member portrait placeholder"></div><b>Team Member 2</b><span class="role">Role 2</span><small>Brief description of expertise and experience.</small></div>
  <div class="member" style="left:304px;top:76px"><div class="avatar" role="img" aria-label="Team member portrait placeholder"></div><b>Team Member 3</b><span class="role">Role 3</span><small>Brief description of expertise and experience.</small></div>
  <div class="member" style="left:36px;top:160px"><div class="avatar" role="img" aria-label="Team member portrait placeholder"></div><b>Team Member 4</b><span class="role">Role 4</span><small>Brief description of expertise and experience.</small></div>
  <div class="member" style="left:170px;top:160px"><div class="avatar" role="img" aria-label="Team member portrait placeholder"></div><b>Team Member 5</b><span class="role">Role 5</span><small>Brief description of expertise and experience.</small></div>
  <div class="member" style="left:304px;top:160px"><div class="avatar" role="img" aria-label="Team member portrait placeholder"></div><b>Team Member 6</b><span class="role">Role 6</span><small>Brief description of expertise and experience.</small></div>
</section>

<section class="slide thanks" style="left:460px;top:872px">
  <div class="brand-mark"><span class="dot"></span>Velmora Quill Industries</div>
  <h2>Thank You</h2>
  <div class="abs orange" style="left:0;right:0;top:116px;text-align:center;font-size:5.2px">Let's Begin Your Digital Transformation Journey Together</div>
  <div class="contact" style="left:35px;top:140px"><div class="ic"><svg width="6" height="5" viewBox="0 0 6 5"><rect x="0.3" y="0.3" width="5.4" height="4.4" fill="none" stroke="#fff" stroke-width="0.6"/><polyline points="0.3,0.5 3,2.6 5.7,0.5" fill="none" stroke="#fff" stroke-width="0.6"/></svg></div><b>Email</b>info@yourcompany.com</div>
  <div class="contact" style="left:155px;top:140px"><div class="ic"><svg width="6" height="6" viewBox="0 0 6 6"><path d="M1,0.5 L2.2,0.5 L2.6,2 L1.9,2.5 C2.3,3.3 2.8,3.8 3.5,4.1 L4,3.4 L5.5,3.8 L5.5,5 C3,5.2 0.8,3 1,0.5Z" fill="#fff"/></svg></div><b>Phone</b>+1 (123) 456-7890</div>
  <div class="contact" style="left:275px;top:140px"><div class="ic"><svg width="5" height="6" viewBox="0 0 5 6"><path d="M2.5,0.3 C1.2,0.3 0.4,1.2 0.4,2.3 C0.4,3.7 2.5,5.7 2.5,5.7 C2.5,5.7 4.6,3.7 4.6,2.3 C4.6,1.2 3.8,0.3 2.5,0.3Z" fill="#fff"/><circle cx="2.5" cy="2.3" r="0.7" fill="#e87722"/></svg></div><b>Address</b>Your Company Address, City, Country</div>
  <div class="abs orange" style="left:0;right:0;top:198px;text-align:center;font-size:4.6px">Contact us today to discuss how we can help your organization achieve</div>
</section>

</body>
</html>
```